BrivoTerna. Lantern of the Steady Harvest. Business card

Professional business card for BrivoTerna (Lantern of the Steady Harvest)
My rationale: Strategy-> Execution-> Results-> Value that lead to the BrivoTerna name: We put the Lantern of the Steady Harvest.
We deliver value to our customers helping them at defining a good strategy (cyan arrow). 90% of well formulated strategies fail due to poor execution so we also consider strategical execution very important (green arrow). Due to the execution we obtain the results (blue arrow). Finally, the results provide feedback to redefine strategy, and the new strategy has to be executed and new results obtained providing new feedback and on and on. It's like a wheel that finally, must create corporate value: value for shareholders, staholders, employees, providers...-

Target Market(s)

CEOs and steering comitees , invewrnent funds

Industry/Entity Type

Business Consultant

Contact Information for Business Card

Teodoro Vinsquel
CEO & Founder
teodoro.vinsquel@brivoterna-example.com
Mobile: +34 655.803.912
www.brivoterna-example.com

Colors

Designer to choose colors to be used in the design.

Requirements
Nice to have
• Nice to hace the words: Strategy, execution, results
• Nice to vave the claim: Lantern of the Steady Harvest
• The three colors should be shown:
• cyan for STRATEGY
• green for EXECUTION
• blue for RESULTS
Should not have
• Complete black background

```html
<!DOCTYPE html>
<html lang="en">
<head>
<meta charset="utf-8">
<title>BrivoTerna – Business Card</title>
<link rel="stylesheet" href="https://fonts.googleapis.com/css2?family=Open+Sans:wght@400;600;700;800&display=swap">
<style>
  :root {
    --brand-blue: #0b3aa6;
    --brand-blue-deep: #082f8c;
    --ink: #222a3a;
    --paper: #ffffff;
    --rule: #d9dde6;
    --stage: #e9ebef;
  }
  * { box-sizing: border-box; margin: 0; padding: 0; }
  html, body {
    width: 1200px; height: 900px; overflow: hidden;
    background: var(--stage);
    font-family: "Open Sans", Arial, sans-serif;
  }
  .canvas {
    position: relative; width: 1200px; height: 900px;
  }
  .card {
    position: absolute; left: 260px;
    width: 680px; height: 388px;
    border-radius: 18px; overflow: hidden;
    box-shadow: 0 6px 18px rgba(20, 30, 60, .18);
  }
  .card--front { top: 40px; background: var(--paper); }
  .card--back { top: 472px; background: var(--brand-blue); }

  .wordmark {
    position: absolute; left: 0; right: 0;
    display: flex; justify-content: center; align-items: center; gap: 12px;
    font-weight: 700; letter-spacing: -1px;
  }
  .wordmark__dot { border-radius: 50%; display: block; }
  .card--front .wordmark { top: 58px; font-size: 54px; color: var(--brand-blue); }
  .card--front .wordmark__dot { width: 22px; height: 22px; background: var(--brand-blue); }
  .card--back .wordmark { top: 120px; font-size: 72px; color: var(--paper); }
  .card--back .wordmark__dot { width: 28px; height: 28px; background: var(--paper); }

  .holder {
    position: absolute; top: 156px; left: 0; right: 0; text-align: center;
  }
  .holder__name {
    font-size: 22px; font-weight: 700; color: var(--brand-blue);
    letter-spacing: .5px; text-transform: uppercase;
  }
  .holder__role { font-size: 15px; color: var(--ink); margin-top: 2px; }

  .divider {
    position: absolute; top: 232px; left: 40px; right: 40px;
    height: 1px; background: var(--rule);
  }

  .contacts {
    position: absolute; top: 246px; left: 40px; right: 40px;
    display: flex; justify-content: space-between; align-items: flex-end;
    font-size: 14.5px; color: var(--ink);
  }
  .contacts__stack { display: flex; flex-direction: column; gap: 6px; align-items: flex-start; }
  .contact-line { display: flex; align-items: center; gap: 6px; white-space: nowrap; }
  .contact-line svg { width: 14px; height: 14px; flex: none; }

  .band { position: absolute; left: 0; bottom: 0; width: 680px; height: 60px; display: block; }
  .band-text {
    position: absolute; bottom: 12px; right: 40px; width: 400px;
    text-align: center; font-weight: 700; font-size: 17px;
    letter-spacing: .5px; text-transform: uppercase;
  }
  .card--front .band-text { color: var(--paper); }
  .card--back .band { height: 72px; }
  .card--back .band-text {
    color: var(--brand-blue); font-weight: 400; font-size: 19px; bottom: 16px; width: 460px; right: 20px;
  }
</style>
</head>
<body>
<main class="canvas">

  <section class="card card--front" aria-label="Business card, front">
    <div class="wordmark"><span class="wordmark__dot"></span>BrivoTerna</div>

    <div class="holder">
      <p class="holder__name">Teodoro Vinsquel</p>
      <p class="holder__role">CEO &amp; Founder</p>
    </div>

    <div class="divider"></div>

    <div class="contacts">
      <div class="contact-line">
        <svg viewBox="0 0 16 16" aria-hidden="true"><circle cx="8" cy="8" r="7" fill="none" stroke="var(--brand-blue)" stroke-width="1.4"/><path d="M5.4 4.6l1.3 1.4-.7 1c.5 1 1.1 1.6 2.1 2.1l1-.7 1.4 1.3-.8 1.2c-2.6-.4-4.6-2.4-5-5z" fill="var(--brand-blue)"/></svg>
        +34 655.803.912
      </div>
      <div class="contacts__stack">
        <div class="contact-line">
          <svg viewBox="0 0 16 16" aria-hidden="true"><rect x="1" y="3.5" width="14" height="9" rx="1" fill="var(--brand-blue)"/><path d="M1.5 4l6.5 5 6.5-5" fill="none" stroke="#fff" stroke-width="1.2"/></svg>
          teodoro.vinsquel@brivoterna-example.com
        </div>
        <div class="contact-line">
          <svg viewBox="0 0 16 16" aria-hidden="true"><circle cx="8" cy="8" r="6.5" fill="var(--brand-blue)"/><path d="M1.5 8h13M8 1.5c-2.5 3-2.5 10 0 13M8 1.5c2.5 3 2.5 10 0 13" fill="none" stroke="#fff" stroke-width=".9"/></svg>
          www.brivoterna-example.com
        </div>
      </div>
    </div>

    <svg class="band" viewBox="0 0 680 60" preserveAspectRatio="none" aria-hidden="true">
      <path d="M0 50 L220 50 C246 50 244 14 270 14 L680 14 L680 60 L0 60 Z" fill="var(--brand-blue)"/>
    </svg>
    <p class="band-text">Strategy &nbsp;-&nbsp; Execution &nbsp;-&nbsp; Results</p>
  </section>

  <section class="card card--back" aria-label="Business card, back">
    <div class="wordmark"><span class="wordmark__dot"></span>BrivoTerna</div>

    <svg class="band" viewBox="0 0 680 72" preserveAspectRatio="none" aria-hidden="true">
      <path d="M0 62 L150 62 C178 62 176 16 204 16 L680 16 L680 72 L0 72 Z" fill="var(--paper)"/>
      <rect x="0" y="66" width="680" height="6" fill="#eef1f7"/>
    </svg>
    <p class="band-text">Lantern of the Steady Harvest</p>
  </section>

</main>
</body>
</html>
```